Current website re-design to a updated look and feel.

We currently have a website www.brightlanefreight.com that we want to give an updated look and feel to. We are a logistics company that competes with Pellwick, Dm Harrowgate, Quill but on a smaller scale. We want something fresh and updated. We have two locations one in downtown Chicago, IL and one in Palatine IL. We are a fun group that also gets the job done. We know we need pictures of both locations and possibly a video, but we need fresh design ideas. The 'who we are' page is really the only page that we currently want to keep. The 'what we do' page needs to be completely re-done from a look and feel for sure.

Target Market(s)

Anyone who uses Truck transportation to move their product. Mainly US manufacturers.

Industry/Entity Type

Logistics

Number of Pages Required

5+ page

Font styles to use
Sans Serif

Colors
5c91c4
0355a3
d0dfed

Requirements
Must have
• The new design must entice people to want to do business with us. The design must have locations for pictures and at least one video which we know we will have to provide. Design must be easy to navigate.

```html
<!DOCTYPE html>
<html lang="en">
<head>
<meta charset="utf-8">
<title>Brightlane Freight</title>
<link href="https://fonts.googleapis.com/css2?family=Lato:wght@400;700;900&display=swap" rel="stylesheet">
<style>
:root{
  --blue:#0355a3;
  --blue-mid:#5c91c4;
  --blue-pale:#d0dfed;
  --ink:#3a3a3a;
  --text:#555;
  --muted:#8a8a8a;
  --gray-band:#f2f2f2;
  --white:#fff;
}
*{box-sizing:border-box;margin:0;padding:0}
html,body{width:1200px;height:3321px;overflow:hidden;background:var(--white)}
body{font-family:"Lato",sans-serif;color:var(--text);position:relative}
.abs{position:absolute}
.btn{position:absolute;background:var(--blue);color:var(--white);font-size:14px;font-weight:700;text-transform:uppercase;display:flex;align-items:center;justify-content:center;gap:8px;border-radius:2px;letter-spacing:.3px}

/* header */
.site-header{position:absolute;left:0;top:0;width:1200px;height:106px;background:var(--white)}
.brand{position:absolute;left:75px;top:22px;display:flex;align-items:center;gap:10px;font-size:38px;font-weight:400;color:var(--blue);letter-spacing:-.5px}
.brand-dot{width:14px;height:14px;background:var(--blue-mid)}
.top-btn{top:20px;height:33px;font-size:13px}
.main-nav{position:absolute;right:75px;top:76px;display:flex;gap:44px;font-size:13px;font-weight:700;color:var(--ink);text-transform:uppercase}
.main-nav .active{color:var(--blue)}

/* hero */
.hero{position:absolute;left:0;top:106px;width:1200px;height:554px;background:linear-gradient(180deg,#5a6470 0%,#7a7f84 35%,#4b4f58 60%,#2e4356 100%)}
.hero-title{position:absolute;left:0;width:1200px;top:170px;text-align:center;color:var(--white);font-weight:900;font-size:42px;line-height:46px;text-transform:uppercase}
.hero-sub{position:absolute;left:230px;width:740px;top:270px;text-align:center;color:var(--white);font-weight:700;font-size:24px;line-height:30px}
.play{left:496px;top:359px;width:208px;height:54px;font-size:18px}
.hero-arrow{position:absolute;top:254px;width:44px;height:44px}

/* founder */
.section-title{position:absolute;font-size:28px;font-weight:700;color:var(--ink);text-transform:uppercase;letter-spacing:.3px}
.founder-text{position:absolute;left:75px;top:752px;width:735px;font-size:14.5px;line-height:24.5px;color:var(--text)}
.founder-photo{position:absolute;left:845px;top:710px;width:279px;height:279px;border-radius:50%;background:radial-gradient(circle at 50% 40%,#e9e3dc 0%,#b9b6b0 60%,#8d8f93 100%);border-bottom:5px solid var(--blue)}
.tagline-art{position:absolute;left:715px;top:930px;width:110px;height:56px;background:linear-gradient(90deg,#e6e6e6,#cfcfcf)}

/* what we do */
.services{position:absolute;left:0;top:1036px;width:1200px;height:463px;background:linear-gradient(180deg,#3b3a3c 0%,#2a2b30 50%,#1d2026 100%)}
.service{position:absolute;top:100px;width:270px;text-align:center;color:var(--white)}
.service-icon{width:102px;height:102px;margin:0 auto;border:3px solid var(--white);border-radius:50%;display:flex;align-items:center;justify-content:center}
.service h3{margin-top:30px;font-size:16px;font-weight:700;text-transform:uppercase;letter-spacing:.3px}
.service p{margin-top:8px;font-size:14.5px;line-height:21px;padding:0 22px}
.service .btn{position:relative;margin:26px auto 0;width:150px;height:48px}

/* vision */
.vm-icon{position:absolute;width:107px;height:107px;border-radius:50%;background:#f4f4f4;border-bottom:4px solid var(--blue);display:flex;align-items:center;justify-content:center}
.vm-title{position:absolute;font-size:17px;font-weight:700;color:var(--blue);text-transform:uppercase}
.vm-text{position:absolute;width:375px;font-size:14px;line-height:22px;color:var(--text)}

/* badges */
.badges{position:absolute;left:0;top:1897px;width:1200px;height:335px;background:var(--gray-band)}
.badge{position:absolute;background:#dcdcdc;border:2px solid #c4c4c4}

/* locations */
.location{position:absolute;top:2342px;width:514px;height:259px;display:flex;align-items:center;justify-content:center;color:var(--white);font-size:26px;font-weight:900;text-transform:uppercase}
.location span{position:relative}

/* updates */
.updates{position:absolute;left:0;top:2663px;width:1200px;height:361px;background:var(--blue-pale)}
.field{position:absolute;height:44px;background:var(--white);font-size:14px;color:#777;padding:0 14px;display:flex;align-items:center}

/* footer */
.foot-head{position:absolute;top:3066px;font-size:14px;font-weight:700;color:var(--blue);text-transform:uppercase}
.foot-list{position:absolute;top:3096px;font-size:13px;line-height:28px;color:var(--text)}
.foot-list .hl{color:var(--blue)}
.social{position:absolute;top:3100px;left:886px;display:flex;gap:14px}
.social i{display:block;width:18px;height:18px;border-radius:50%;background:#a9a9a9}
</style>
</head>
<body>

<header class="site-header">
  <div class="brand"><span class="brand-dot"></span>Brightlane Freight</div>
  <div class="btn top-btn" style="left:937px;width:96px">
    <svg width="14" height="12" viewBox="0 0 14 12"><path d="M1 1h12v7H6l-3 3V8H1z" fill="#fff"/></svg>Chat</div>
  <div class="btn top-btn" style="left:1037px;width:96px">
    <svg width="12" height="12" viewBox="0 0 12 12"><circle cx="6" cy="4" r="3" fill="#fff"/><path d="M0 12c0-4 3-5 6-5s6 1 6 5z" fill="#fff"/></svg>Log In</div>
  <nav class="main-nav">
    <span class="active">Home</span><span>What We Do</span><span>How We Do It</span><span>Who We Are</span><span>Tracking</span><span>Contact</span>
  </nav>
</header>

<section class="hero" role="img" aria-label="Photo of a container port with stacked shipping containers and cranes">
  <h1 class="hero-title">Welcome to<br>Brightlanefreight</h1>
  <p class="hero-sub">We are a logistics company that competes with Pellwick, Dm Harrowgate, Quill but on a smaller scale.</p>
  <div class="btn play">
    <svg width="26" height="26" viewBox="0 0 26 26"><circle cx="13" cy="13" r="12" fill="#fff"/><path d="M10 7l9 6-9 6z" fill="#0355a3"/></svg>Play Video</div>
  <svg class="hero-arrow" style="left:58px" viewBox="0 0 44 44"><circle cx="22" cy="22" r="20" fill="none" stroke="#fff" stroke-width="2"/><path d="M25 14l-8 8 8 8" fill="none" stroke="#fff" stroke-width="2.5"/></svg>
  <svg class="hero-arrow" style="left:1098px" viewBox="0 0 44 44"><circle cx="22" cy="22" r="20" fill="none" stroke="#fff" stroke-width="2"/><path d="M19 14l8 8-8 8" fill="none" stroke="#fff" stroke-width="2.5"/></svg>
</section>

<section class="founder">
  <h2 class="section-title" style="left:75px;top:706px">Welcome from our founder</h2>
  <div class="founder-text">
    <p>Brightlane Freight welcomes you to our growing family of clients! We have over 26 years of experience in helping people solve their logistics needs from coast-to-coast. We also provide friendly, exceptional service that makes it easy to do business with us. Give us a call today and experience the difference for yourself!</p>
    <p>"Our service commitment begins from the moment you contact us. We appreciate your trust, and we go the extra mile to ensure that your freight is handled with care and expediency.</p>
  </div>
  <div class="btn" style="left:75px;top:943px;width:151px;height:47px">Read More</div>
  <div class="tagline-art" role="img" aria-label="Hand lettered slogan with a small chair sketch"></div>
  <div class="founder-photo" role="img" aria-label="Portrait photo of the company founder"></div>
</section>

<section class="services" role="img" aria-label="Dark photo of railway tracks at dusk">
  <h2 class="section-title" style="left:0;width:1200px;top:48px;text-align:center;color:#fff">What we do</h2>
  <div class="service" style="left:60px">
    <div class="service-icon"><svg width="44" height="44" viewBox="0 0 44 44"><path d="M22 4c2 0 3 2 3 4v10l15 9v4l-15-5v9l5 4v3l-8-2-8 2v-3l5-4v-9L4 31v-4l15-9V8c0-2 1-4 3-4z" fill="#fff"/></svg></div>
    <h3>Freight Management</h3>
    <p>We strive for a perfect delivery and promise to be there for anything you...</p>
    <div class="btn">Read More</div>
  </div>
  <div class="service" style="left:330px">
    <div class="service-icon"><svg width="48" height="36" viewBox="0 0 48 36"><rect x="2" y="4" width="28" height="22" fill="#fff"/><path d="M32 10h8l6 8v8H32z" fill="#fff"/><circle cx="11" cy="29" r="5" fill="#fff" stroke="#2a2b30" stroke-width="2"/><circle cx="38" cy="29" r="5" fill="#fff" stroke="#2a2b30" stroke-width="2"/></svg></div>
    <h3>Transportation</h3>
    <p>With a combined 500+ years of industry experience between all employees...</p>
    <div class="btn">Read More</div>
  </div>
  <div class="service" style="left:600px">
    <div class="service-icon"><svg width="46" height="40" viewBox="0 0 46 40"><path d="M2 14L23 2l21 12v24H2z" fill="#fff"/><rect x="10" y="18" width="26" height="20" fill="#2a2b30"/><rect x="12" y="21" width="22" height="3" fill="#fff"/><rect x="12" y="27" width="22" height="3" fill="#fff"/><rect x="12" y="33" width="22" height="3" fill="#fff"/></svg></div>
    <h3>Warehouse &amp; Distribution</h3>
    <p>Our secure facility can accommodate large or small quantities of product.</p>
    <div class="btn">Read More</div>
  </div>
  <div class="service" style="left:870px">
    <div class="service-icon"><svg width="36" height="48" viewBox="0 0 36 48"><rect x="6" y="2" width="24" height="16" rx="3" fill="#fff"/><rect x="10" y="6" width="16" height="7" fill="#2a2b30"/><rect x="4" y="20" width="28" height="22" fill="#fff"/><rect x="2" y="42" width="8" height="5" fill="#fff"/><rect x="26" y="42" width="8" height="5" fill="#fff"/></svg></div>
    <h3>Carriers</h3>
    <p>Are you a carrier looking to work with Brightlane? Click here to find out why...</p>
    <div class="btn">Read More</div>
  </div>
</section>

<section class="vision">
  <h2 class="section-title" style="left:0;width:1200px;top:1541px;text-align:center">Brightlane Freight vision and mission</h2>
  <div class="vm-icon" style="left:75px;top:1621px">
    <svg width="50" height="50" viewBox="0 0 50 50"><path d="M8 22l28-12 4 9-28 12z" fill="#444"/><rect x="36" y="6" width="7" height="14" transform="rotate(-23 39 13)" fill="#444"/><path d="M22 28l-8 18M24 28l8 18M23 28v18" stroke="#444" stroke-width="3"/></svg>
  </div>
  <div class="vm-title" style="left:204px;top:1617px">Brightlane Vision</div>
  <p class="vm-text" style="left:204px;top:1646px">Brightlane vision is to be the premier third party logistics solution in North America. We will become premier by providing superior customer service, efficient and cost effective warehousing and distribution solutions.</p>
  <div class="vm-icon" style="left:627px;top:1621px">
    <svg width="50" height="50" viewBox="0 0 50 50"><circle cx="25" cy="25" r="20" fill="none" stroke="#444" stroke-width="4"/><circle cx="25" cy="25" r="11" fill="none" stroke="#444" stroke-width="4"/><circle cx="25" cy="25" r="3" fill="#444"/><path d="M25 25L44 6" stroke="#444" stroke-width="3"/></svg>
  </div>
  <div class="vm-title" style="left:755px;top:1617px">Brightlane Mission</div>
  <p class="vm-text" style="left:755px;top:1646px">Brightlane's mission is to provide the most thorough and satisfying third-party logistics experience for its customers. Brightlane uses leading technologies and an industry experienced staff to deliver an unparalleled customer service experience.</p>
  <div class="btn" style="left:509px;top:1796px;width:182px;height:48px">Request a Quote</div>
</section>

<section class="badges" aria-label="Awards and certifications">
  <div class="badge" style="left:75px;top:49px;width:152px;height:93px"></div>
  <div class="badge" style="left:248px;top:49px;width:248px;height:93px"></div>
  <div class="badge" style="left:518px;top:49px;width:182px;height:93px"></div>
  <div class="badge" style="left:721px;top:49px;width:200px;height:93px"></div>
  <div class="badge" style="left:946px;top:61px;width:180px;height:70px;border-radius:35px"></div>
  <div class="badge" style="left:371px;top:169px;width:120px;height:115px;border-radius:50%"></div>
  <div class="badge" style="left:527px;top:180px;width:50px;height:95px"></div>
  <div class="badge" style="left:620px;top:169px;width:100px;height:100px;border-radius:50%"></div>
  <div class="badge" style="left:750px;top:169px;width:84px;height:124px"></div>
</section>

<section class="locations">
  <h2 class="section-title" style="left:0;width:1200px;top:2274px;text-align:center">Our locations</h2>
  <div class="location" style="left:75px;background:linear-gradient(180deg,#4a4e55,#2d3036)" role="img" aria-label="Photo of the downtown Chicago skyline"><span>Downtown Chicago, IL</span></div>
  <div class="location" style="left:613px;background:linear-gradient(180deg,#6a6c70,#4d4a45)" role="img" aria-label="Photo of Palatine town buildings"><span>Palatine IL</span></div>
</section>

<section class="updates">
  <h2 class="section-title" style="left:0;width:1200px;top:44px;text-align:center">Get updates</h2>
  <p class="abs" style="left:0;width:1200px;top:96px;text-align:center;font-size:14px">We occasionally send out news and related industry articles. Sign up and we promise to deliver quality information to you.</p>
  <div class="field" style="left:255px;top:147px;width:332px">First Name</div>
  <div class="field" style="left:613px;top:147px;width:335px">Last Name</div>
  <div class="field" style="left:255px;top:200px;width:332px">Email Address</div>
  <div class="field" style="left:613px;top:200px;width:335px">Organization</div>
  <div class="btn" style="left:509px;top:271px;width:182px;height:48px">Submit</div>
</section>

<footer class="site-footer">
  <div class="brand" style="top:3068px;font-size:30px"><span class="brand-dot"></span>Brightlane</div>
  <p class="abs" style="left:75px;top:3134px;font-size:13px;line-height:22px">Copyright © 2017. Company Name.<br>All Right Reserved</p>
  <div class="foot-head" style="left:432px">Site Map</div>
  <div class="foot-list" style="left:432px">What We Do<br>How We Do It<br>Who We Are<br>Tracking<br>Chat<br>Contact</div>
  <div class="foot-head" style="left:640px">Contact Info</div>
  <div class="foot-list" style="left:640px">418 W Orchard Ave Suite 210<br>Palatine, IL 60067<br><span class="hl">Office Phone: 555.014.3300</span><br><span class="hl">Warehouse: 555.014.3302</span><br><span class="hl">Fax: 555.014.3301</span></div>
  <div class="foot-head" style="left:886px">Follow Us</div>
  <div class="social"><i></i><i></i><i></i><i></i><i></i><i></i></div>
</footer>

</body>
</html>
```